Pinecrest Valley Outfitters Banner

We are looking for a banner ad that we will run on DailyLarkPost.com the size is 758x120 and also a matching one that is 300x250 can be animated or static.final graphics will need to be submitted in jpg, gif or similar format. Our shop is a firearms business called "Pinecrest Valley Outfitters" located at 417 Route 52 South, Bramwell Ms. 39247 phone is 662-574-3168 . it need to be modern and eye catching and be more geared to the tactical side. Our website is
pinecrestvoutfitters.com the banners DO NOT have to match website. would like a DIFFERENT LOOK than my website

```html
<!DOCTYPE html>
<html lang="en">
<head>
<meta charset="utf-8">
<title>Pinecrest Valley Outfitters – Banner Set</title>
<link rel="stylesheet" href="https://fonts.googleapis.com/css2?family=Alfa+Slab+One&family=PT+Sans:wght@700&family=Roboto+Condensed:wght@500&display=swap">
<style>
  :root {
    --page: #ffffff;
    --accent-green: #5b8c1f;
    --ink: #0b0b0b;
    --red-deep: #6e0a0c;
    --red-bright: #d0151a;
    --gold: #f7c21a;
    --white: #ffffff;
    --steel: #9a9a9a;
  }
  * { margin: 0; padding: 0; box-sizing: border-box; }
  html, body { width: 1200px; height: 930px; overflow: hidden; background: var(--page); }
  .sheet { position: relative; width: 1200px; height: 930px; }
  .sheet__rule { position: absolute; left: 0; top: 0; width: 100%; height: 5px; background: var(--accent-green); }

  .banner {
    position: absolute; overflow: hidden; background: var(--ink);
    box-shadow: 3px 4px 6px rgba(0,0,0,.45);
  }
  .banner--leaderboard { left: 105px; top: 208px; width: 1000px; height: 160px; }
  .banner--rectangle { left: 395px; top: 465px; width: 395px; height: 332px; }

  .banner__backdrop { position: absolute; inset: 0; }
  .banner--leaderboard .banner__backdrop {
    background:
      radial-gradient(ellipse 220px 120px at 120px 30px, var(--red-bright), transparent 70%),
      radial-gradient(ellipse 260px 90px at 700px 20px, var(--red-deep), transparent 75%),
      radial-gradient(ellipse 240px 100px at 920px 150px, var(--red-bright), transparent 70%),
      radial-gradient(ellipse 300px 80px at 500px 165px, var(--red-deep), transparent 75%),
      var(--ink);
  }
  .banner--rectangle .banner__backdrop {
    background:
      radial-gradient(ellipse 260px 130px at 330px 20px, var(--red-deep), transparent 75%),
      radial-gradient(ellipse 200px 120px at 40px 190px, var(--red-bright), transparent 70%),
      radial-gradient(ellipse 160px 140px at 395px 260px, var(--red-bright), transparent 70%),
      var(--ink);
  }

  .faint-art {
    position: absolute; left: 217px; top: 15px; width: 185px; height: 95px;
    background: radial-gradient(ellipse at center, rgba(60,60,60,.55), transparent 70%);
  }

  .product-list { position: absolute; left: 37px; top: 14px; list-style: none; }
  .product-list li, .product-line {
    font-family: "Alfa Slab One", serif; color: var(--white); text-transform: uppercase;
    text-shadow: 2px 2px 0 #000, -1px -1px 0 #000;
  }
  .product-list li { font-size: 26px; line-height: 47px; letter-spacing: .5px; }
  .initial { color: var(--gold); }

  .headline { position: absolute; font-family: "PT Sans", sans-serif; font-weight: 700; line-height: 1; text-shadow: 2px 2px 3px rgba(0,0,0,.7); }
  .headline__top { display: block; color: var(--white); }
  .headline__main { display: block; color: var(--gold); }
  .banner--leaderboard .headline { left: 450px; top: 24px; }
  .banner--leaderboard .headline__top { font-size: 23px; }
  .banner--leaderboard .headline__main { font-size: 50px; margin-top: 2px; }
  .banner--rectangle .headline { left: 33px; top: 14px; }
  .banner--rectangle .headline__top { font-size: 27px; }
  .banner--rectangle .headline__main { font-size: 54px; margin-top: 2px; }

  .product-art { position: absolute; background: linear-gradient(160deg, #2a2a2a, #050505); border-radius: 4px; }
  .banner--leaderboard .product-art { left: 668px; top: 26px; width: 97px; height: 69px; }
  .banner--rectangle .product-art { left: 258px; top: 17px; width: 105px; height: 74px; }

  .brand-mark {
    position: absolute; display: flex; align-items: center; gap: 7px;
    font-family: "PT Sans", sans-serif; font-weight: 700; color: var(--white);
    font-size: 17px; line-height: 1.15;
  }
  .brand-mark__dot { flex: none; width: 20px; height: 20px; border-radius: 50%; background: var(--steel); }
  .banner--leaderboard .brand-mark { left: 850px; top: 48px; }
  .banner--rectangle .brand-mark { left: 143px; top: 135px; }

  .contact { position: absolute; font-family: "Roboto Condensed", sans-serif; font-weight: 500; color: var(--white); white-space: nowrap; letter-spacing: .4px; }
  .contact__phone { color: var(--gold); }
  .banner--leaderboard .contact { left: 303px; top: 119px; font-size: 21px; }
  .banner--rectangle .contact { left: 0; width: 100%; text-align: center; top: 269px; font-size: 19px; line-height: 26px; }

  .product-line { position: absolute; left: 0; width: 100%; top: 235px; text-align: center; font-size: 20px; }

  .trim { position: absolute; bottom: 0; height: 4px; background: var(--gold); }
</style>
</head>
<body>
<main class="sheet">
  <div class="sheet__rule"></div>

  <section class="banner banner--leaderboard" aria-label="Leaderboard banner 758 by 120">
    <div class="banner__backdrop" role="img" aria-label="Flowing red satin waves on black"></div>
    <div class="faint-art" role="img" aria-label="Faint handgun silhouette"></div>
    <ul class="product-list">
      <li><span class="initial">F</span>irearms</li>
      <li><span class="initial">A</span>mmo</li>
      <li><span class="initial">A</span>ccessories</li>
    </ul>
    <h1 class="headline"><span class="headline__top">Pinecrest Valley</span><span class="headline__main">Outfitters</span></h1>
    <div class="product-art" role="img" aria-label="Black handgun silhouette"></div>
    <div class="brand-mark"><span class="brand-mark__dot"></span><span>Pinecrest<br>Valley<br>Outfitters</span></div>
    <p class="contact">417 Route 52 South, Bramwell Ms. 39247&nbsp; Phone- <span class="contact__phone">662-574-3168</span></p>
    <div class="trim" style="left:0;width:245px"></div>
    <div class="trim" style="left:255px;width:330px"></div>
    <div class="trim" style="left:600px;width:400px"></div>
  </section>

  <section class="banner banner--rectangle" aria-label="Medium rectangle banner 300 by 250">
    <div class="banner__backdrop" role="img" aria-label="Flowing red satin waves on black"></div>
    <h2 class="headline"><span class="headline__top">Pinecrest Valley</span><span class="headline__main">Outfitters</span></h2>
    <div class="product-art" role="img" aria-label="Black handgun silhouette"></div>
    <div class="brand-mark"><span class="brand-mark__dot"></span><span>Pinecrest<br>Valley<br>Outfitters</span></div>
    <p class="product-line"><span class="initial">F</span>irearms <span class="initial">A</span>mmo <span class="initial">A</span>ccessories</p>
    <p class="contact">417 Route 52 South, Bramwell Ms. 39247<br>Phone- <span class="contact__phone">662-574-3168</span></p>
    <div class="trim" style="left:8px;width:80px"></div>
    <div class="trim" style="left:98px;width:190px"></div>
    <div class="trim" style="left:298px;width:76px"></div>
  </section>
</main>
</body>
</html>
```